Stonebridge Building and Projects business cards

A business card with watermark background (construction work)

Company logo attached

Home improvement projects
House renovations
Bathroom and kitchen renovations
House extensions
New builds and granny flats

Director Omar Haddani
(Phone number)
omar@sbpbuilding.com.au
(Instagram logo) sbp_building

```html
<!DOCTYPE html>
<html lang="en">
<head>
<meta charset="utf-8">
<title>Stonebridge Building and Projects – Business Cards</title>
<link rel="stylesheet" href="https://fonts.googleapis.com/css2?family=Arimo:wght@400;700&display=swap">
<style>
  :root {
    --stage: #c9cacc;
    --brand-blue: #2469b0;
    --brand-blue-light: #2f78bd;
    --card-white: #ffffff;
    --ink-white: #ffffff;
    --shadow: rgba(0, 0, 0, 0.22);
  }
  * { box-sizing: border-box; margin: 0; padding: 0; }
  html, body {
    width: 1200px;
    height: 800px;
    overflow: hidden;
    background: var(--stage);
    font-family: "Arimo", Arial, sans-serif;
  }
  .canvas {
    width: 1200px;
    height: 800px;
    display: flex;
    align-items: center;
    justify-content: center;
    gap: 40px;
  }
  .card {
    width: 540px;
    height: 309px;
    border-radius: 22px;
    box-shadow: 0 10px 28px var(--shadow);
    position: relative;
    overflow: hidden;
  }

  /* Contact side */
  .card--contact {
    background: linear-gradient(135deg, var(--brand-blue-light), var(--brand-blue));
    color: var(--ink-white);
  }
  .identity {
    position: absolute;
    left: 46px;
    top: 92px;
    width: 190px;
    text-align: right;
  }
  .identity__name {
    font-weight: 700;
    font-size: 23px;
    letter-spacing: 0.5px;
    text-transform: uppercase;
    line-height: 1.1;
  }
  .identity__role {
    font-size: 15px;
    margin-top: 4px;
  }
  .divider {
    position: absolute;
    left: 256px;
    top: 78px;
    width: 1px;
    height: 98px;
    background: var(--ink-white);
    opacity: 0.85;
  }
  .contact-list {
    position: absolute;
    left: 276px;
    top: 78px;
    list-style: none;
    font-size: 13px;
    line-height: 1;
  }
  .contact-list__item {
    display: flex;
    align-items: center;
    gap: 8px;
    height: 24.5px;
  }
  .contact-list__icon {
    width: 12px;
    height: 12px;
    flex: none;
  }
  .services {
    position: absolute;
    left: 0;
    right: 0;
    bottom: 40px;
    text-align: center;
    font-size: 13.5px;
    line-height: 1.45;
  }

  /* Brand side */
  .card--brand {
    background: var(--card-white);
    display: flex;
    align-items: center;
    justify-content: center;
  }
  .brand-name {
    display: flex;
    align-items: center;
    gap: 12px;
    color: var(--brand-blue);
    font-weight: 700;
    font-size: 24px;
    line-height: 1.2;
  }
  .brand-name__mark {
    width: 18px;
    height: 18px;
    background: var(--brand-blue);
    flex: none;
  }
  .brand-name__text { max-width: 300px; }
</style>
</head>
<body>
<main class="canvas">
  <section class="card card--contact" aria-label="Contact side">
    <div class="identity">
      <p class="identity__name">Omar Haddani</p>
      <p class="identity__role">Director</p>
    </div>
    <div class="divider"></div>
    <ul class="contact-list">
      <li class="contact-list__item">
        <svg class="contact-list__icon" viewBox="0 0 24 24" aria-hidden="true"><path fill="#fff" d="M6.6 10.8a15.1 15.1 0 0 0 6.6 6.6l2.2-2.2c.3-.3.7-.4 1-.2 1.1.4 2.3.6 3.6.6.6 0 1 .4 1 1V20c0 .6-.4 1-1 1A17 17 0 0 1 3 4c0-.6.4-1 1-1h3.5c.6 0 1 .4 1 1 0 1.3.2 2.5.6 3.6.1.3 0 .7-.2 1z"/></svg>
        <span>402-318-7741</span>
      </li>
      <li class="contact-list__item">
        <svg class="contact-list__icon" viewBox="0 0 24 24" aria-hidden="true"><path fill="#fff" d="M2 5h20v14H2z"/><path fill="none" stroke="#2469b0" stroke-width="2" d="M3 6l9 7 9-7"/></svg>
        <span>omar@sbpbuilding.com.au</span>
      </li>
      <li class="contact-list__item">
        <svg class="contact-list__icon" viewBox="0 0 24 24" aria-hidden="true"><g fill="none" stroke="#fff" stroke-width="2"><circle cx="12" cy="12" r="10"/><ellipse cx="12" cy="12" rx="4" ry="10"/><path d="M2 12h20"/></g></svg>
        <span>sbpbuilding.com.au</span>
      </li>
      <li class="contact-list__item">
        <svg class="contact-list__icon" viewBox="0 0 24 24" aria-hidden="true"><circle cx="12" cy="12" r="9" fill="none" stroke="#fff" stroke-width="2"/></svg>
        <span>sbp_building</span>
      </li>
    </ul>
    <p class="services">
      Home improvement projects :: House renovations :: House extensions<br>
      Bathroom &amp; kitchen renovations :: New builds &amp; granny flats
    </p>
  </section>

  <section class="card card--brand" aria-label="Brand side">
    <div class="brand-name">
      <span class="brand-name__mark"></span>
      <span class="brand-name__text">Stonebridge Building and Projects</span>
    </div>
  </section>
</main>
</body>
</html>
```